Family business needs stationery redesign with new logo

Family owned company, established in 1987 wanting a brand 'refresh'. We are an electrical, refrigeration and construction company based in the Barkly Region Northern Territory, Australia. We have a new logo we would like to use which is uploaded along with our current letterhead and email signature. We are also dropping the word 'contractors' so please do not include this on any designs. Please note also, the 'orange' color used in our logo and designs should be Northern Territory red ochre which is as follows:

RGB (Hex): #C75B12
PantoneĀ® 159 C
CMYK: 1 / 74 / 100 / 7

We are needing our stationery redesigned using our new logo. Please include letterheads, business cards, envelopes, and email signatures.

We currently use our business letterheads for quotations, invoices, letters, HR matters, and internal memos.

We also need a separate simplified letterhead for internal paperwork such as employee leave forms, meeting agendas, and meeting minutes etc.

Reason: Needing more submissions of full package designs. We are wanting all our stationery, including business cards, letterheads, email signatures, envelopes, etc to be cohesive. We also require ALL the information, as supplied on our template letterhead, to be included on the new letterhead designs. including electrical license no.etc Thank you, R&W

Reason: needing more time as work has got in the way of looking over designs. A lot of designs not meeting the brief/criteria.

Industry/Entity Type

Business

Colors
0355a3
f37122

Requirements
Must have
• The 'orange' color used in the designs should be Northern Territory red ochre which is as follows:
• RGB (Hex): #C75B12
• PantoneĀ® 159 C
• CMYK: 1 / 74 / 100 / 7
• ***MUST INCLUDE ALL INFORMATION THAT IS ON OUR CURRENT LETTERHEAD***
Should not have
• Please do not include the word 'contractors'

```html
<!DOCTYPE html>
<html lang="en">
<head>
<meta charset="utf-8">
<title>R&amp;W Stationery</title>
<link href="https://fonts.googleapis.com/css2?family=Source+Sans+3:wght@400;600;700&display=swap" rel="stylesheet">
<style>
:root{
  --navy:#253368;
  --ochre:#dc5d20;
  --ink:#555a60;
  --paper:#ffffff;
  --stage:#2b2d2e;
  --faint:#eeeeee;
}
*{box-sizing:border-box;margin:0;padding:0}
html,body{width:1200px;height:922px;overflow:hidden}
body{background:var(--stage);font-family:"Source Sans 3",Arial,sans-serif;color:var(--ink);position:relative}
.sheet{position:absolute;background:var(--paper);box-shadow:0 2px 6px rgba(0,0,0,.5)}
.wordmark{font-weight:700;color:var(--navy);line-height:1;letter-spacing:1px;position:absolute}
.wordmark.light{color:var(--paper)}
.wordmark.ghost{color:var(--faint)}
.lines{position:absolute;font-size:8px;line-height:10px}
.lines .icon{display:inline-block;width:6px;height:6px;border-radius:50%;background:var(--ochre);margin-right:3px;vertical-align:middle}
.name{color:var(--navy);font-weight:700}
.accent{color:var(--ochre)}

/* letterhead */
.letterhead{left:21px;top:190px;width:549px;height:710px}
.letterhead .wordmark{left:36px;top:40px;font-size:46px}
.letterhead .address{left:379px;top:33px}
.letterhead .contact{left:379px;top:69px}
.letterhead .legal{position:absolute;left:0;right:0;top:668px;text-align:center;font-size:7.5px}
.letterhead .legal .sep{color:var(--ochre);margin:0 3px}
.letterhead .band{position:absolute;left:0;right:0;top:686px;height:24px;background:var(--navy);border-top:2px solid var(--ochre);color:var(--paper);font-size:8px;text-align:center;line-height:22px}

/* card landscape */
.card-wide{left:607px;top:21px;width:359px;height:141px;overflow:hidden}
.card-wide .wordmark{left:20px;top:17px;font-size:21px}
.card-wide .wordmark.ghost{left:240px;top:2px;font-size:58px}
.card-wide .title{position:absolute;left:16px;top:59px;font-size:7px;line-height:9px}
.card-wide .title .name{font-size:11px}
.card-wide .contact{left:16px;top:90px;font-size:7px;line-height:9px}
.card-wide .address{left:165px;top:90px;font-size:7px;line-height:9px;border-left:1px solid var(--ink);padding-left:7px}

/* card small */
.card-small{left:607px;top:190px;width:226px;height:130px;border-radius:6px}
.card-small .wordmark{left:158px;top:17px;font-size:20px}
.card-small .title{position:absolute;left:11px;top:49px;width:204px;font-size:5.5px;line-height:7px;border-bottom:1px solid #a9abc4;padding-bottom:5px}
.card-small .title .name{font-size:8.5px}
.card-small .contact{left:11px;top:82px;font-size:5.5px;line-height:7.5px}
.card-small .contact .icon{width:4px;height:4px}
.card-small .address{right:11px;top:97px;font-size:5.5px;line-height:7.5px;text-align:right}

/* card reverse */
.card-back{left:847px;top:190px;width:226px;height:130px;border-radius:6px;background:var(--ochre)}
.card-back .wordmark{left:0;right:0;top:50px;text-align:center;font-size:30px}
.card-back .services{position:absolute;left:0;right:0;top:111px;text-align:center;color:var(--paper);font-size:6px}

/* envelope back */
.envelope-back{left:607px;top:366px;width:574px;height:250px}
.envelope-back svg{position:absolute;left:0;top:0}
.envelope-back .wordmark{left:0;right:0;top:26px;text-align:center;font-size:20px}

/* envelope front */
.envelope-front{left:607px;top:650px;width:574px;height:250px;overflow:hidden}
.envelope-front .wordmark{left:30px;top:22px;font-size:34px}
.envelope-front .wordmark.ghost{left:350px;top:150px;font-size:108px}
.envelope-front .address{left:25px;top:79px;font-size:8px;line-height:10.5px}
</style>
</head>
<body>

<section class="sheet letterhead">
  <div class="wordmark">R&amp;W</div>
  <div class="lines address">PO Box 4410, 52 Ridge St<br>Barrow Flats NT 0870</div>
  <div class="lines contact">
    <span class="icon"></span>08 8000 1234<br>
    <span class="icon"></span>08 8000 5678<br>
    <span class="icon"></span>dana@rwservices.com.au<br>
    <span class="icon"></span>www.rwservices.com.au
  </div>
  <div class="legal">ABN 12 345 678 901<span class="sep">|</span>Refrigerant Trading Authorisation AU09876<span class="sep">|</span>NT Electrical Contractors License 09876</div>
  <div class="band">Electrical <span class="accent">•</span> Refrigeration <span class="accent">•</span> Building Services</div>
</section>

<section class="sheet card-wide">
  <div class="wordmark ghost">R&amp;W</div>
  <div class="wordmark">R&amp;W</div>
  <div class="title"><span class="name">Dana Whitfield</span><br>Corporate Services Manager, R&amp;W Services</div>
  <div class="lines contact">
    <span class="icon"></span>08 8000 1234<br>
    <span class="icon"></span>0400 555 018<br>
    <span class="icon"></span>08 8000 5678<br>
    <span class="icon"></span>dana@rwservices.com.au
  </div>
  <div class="lines address">PO Box 4410<br>52 Ridge St<br>Barrow Flats NT 0870<br><span class="accent">www.rwservices.com.au</span></div>
</section>

<section class="sheet card-small">
  <div class="wordmark">R&amp;W</div>
  <div class="title"><span class="name">Dana Whitfield</span><br>Corporate Services Manager<br>R&amp;W Services</div>
  <div class="lines contact">
    <span class="icon"></span>08 8000 1234<br>
    <span class="icon"></span>0400 555 018<br>
    <span class="icon"></span>08 8000 5678<br>
    <span class="icon"></span>dana@rwservices.com.au<br>
    <span class="icon"></span>www.rwservices.com.au
  </div>
  <div class="lines address">PO Box 4410<br>52 Ridge St<br>Barrow Flats NT 0870</div>
</section>

<section class="sheet card-back">
  <div class="wordmark light">R&amp;W</div>
  <div class="services">Electrical • Refrigeration • Building Services</div>
</section>

<section class="sheet envelope-back">
  <svg width="574" height="80" viewBox="0 0 574 80" aria-hidden="true">
    <path d="M0 0H574L566 42Q563 72 540 74H32Q10 72 8 42Z" fill="var(--ochre)"/>
  </svg>
  <div class="wordmark light">R&amp;W</div>
</section>

<section class="sheet envelope-front">
  <div class="wordmark ghost">R&amp;W</div>
  <div class="wordmark">R&amp;W</div>
  <div class="lines address">PO Box 4410, 52 Ridge St<br>Barrow Flats NT 0870</div>
</section>

</body>
</html>
```